Business Card Design for company

We want new business cards. We'd like something different-- yet still highly professional. Our tagline is Providing leadership, delivering success. Stock photos are ok, as long as they are relevant and look upscale.

Target Market(s)

Architecture/Business Management Consulting/Engineering Consulting

Contact Information for Business Card

dark gray background with pops of blue might be good, but you tell me. You're the designers. Rounded corners might be nice, but again, you tell me.

Font styles to use
Serif
Sans Serif

Colors
3276b5
5c5c5c
9d9d9d
fbfbfb

Requirements
Nice to have
• Something different, but still very professional.

```html
<!DOCTYPE html>
<html lang="en">
<head>
<meta charset="UTF-8">
<title>Harlow Meridian – Business Card</title>
<link rel="stylesheet" href="https://fonts.googleapis.com/css2?family=Montserrat:wght@400;500;600;700&display=swap">
<style>
  :root {
    --stage: #2b2b2b;
    --card: #6f6f6f;
    --ink: #fbfbfb;
    --ink-soft: #e6e6e6;
    --shadow: rgba(0,0,0,0.45);
  }
  * { margin: 0; padding: 0; box-sizing: border-box; }
  html, body {
    width: 1200px; height: 900px; overflow: hidden;
    background: var(--stage);
    font-family: "Montserrat", Arial, sans-serif;
    color: var(--ink);
  }
  .card {
    position: absolute;
    left: 250px;
    width: 700px; height: 400px;
    background: var(--card);
    box-shadow: 0 10px 30px var(--shadow);
  }
  .card--front { top: 40px; }
  .card--back { top: 470px; }

  .brand-name {
    font-weight: 700;
    color: var(--ink);
    letter-spacing: 0.04em;
    text-transform: uppercase;
    line-height: 1.05;
  }
  .card--front .brand-name {
    position: absolute; left: 0; right: 0; top: 140px;
    text-align: center; font-size: 54px;
  }
  .card--back .brand-name {
    position: absolute; left: 40px; top: 140px;
    font-size: 38px;
  }

  .contact {
    position: absolute; left: 390px; top: 62px; width: 290px;
  }
  .contact__name {
    font-size: 24px; font-weight: 600; letter-spacing: 0.08em;
  }
  .contact__title {
    font-size: 14px; font-weight: 400; color: var(--ink-soft); margin-top: 2px;
  }
  .divider {
    width: 44px; height: 2px; background: var(--ink); margin: 12px 0 14px;
  }
  .contact__address {
    font-size: 15px; font-weight: 400; line-height: 1.35;
  }
  .contact__list { list-style: none; }
  .contact__item {
    display: flex; align-items: center; gap: 18px;
    font-size: 16px; font-weight: 400; height: 33px;
  }
  .contact__item svg { width: 20px; height: 20px; flex: none; }
</style>
</head>
<body>

<section class="card card--front">
  <div class="brand-name">Harlow Meridian</div>
</section>

<section class="card card--back">
  <div class="brand-name">Harlow<br>Meridian</div>

  <div class="contact">
    <div class="contact__name">DANIEL PRESCOTT</div>
    <div class="contact__title">CEO | Founder</div>
    <div class="divider"></div>
    <div class="contact__address">480 Alder Crest Road,<br>Suite 210 Fairbrook, NY 11800</div>
    <div class="divider"></div>
    <ul class="contact__list">
      <li class="contact__item">
        <svg viewBox="0 0 24 24" aria-hidden="true"><path fill="#fbfbfb" d="M6.6 10.8a15.1 15.1 0 006.6 6.6l2.2-2.2a1 1 0 011-.25 11.4 11.4 0 003.6.57 1 1 0 011 1V20a1 1 0 01-1 1A17 17 0 013 4a1 1 0 011-1h3.5a1 1 0 011 1c0 1.25.2 2.45.57 3.57a1 1 0 01-.25 1z"/></svg>
        555-014-2024
      </li>
      <li class="contact__item">
        <svg viewBox="0 0 24 24" aria-hidden="true"><path fill="#fbfbfb" d="M7 2h8l3 3v4H7zM4 10h16a1 1 0 011 1v9a1 1 0 01-1 1H4a1 1 0 01-1-1v-9a1 1 0 011-1zm3 3v2h2v-2zm4 0v2h2v-2zm4 0v2h2v-2zm-8 4v2h2v-2zm4 0v2h2v-2zm4 0v2h2v-2z"/></svg>
        555-014-2023
      </li>
      <li class="contact__item">
        <svg viewBox="0 0 24 24" aria-hidden="true"><rect x="2" y="5" width="20" height="14" fill="none" stroke="#fbfbfb" stroke-width="2"/><path d="M2 5l10 8 10-8" fill="none" stroke="#fbfbfb" stroke-width="2"/></svg>
        prescott@harlowmeridian.com
      </li>
      <li class="contact__item">
        <svg viewBox="0 0 24 24" aria-hidden="true"><g fill="none" stroke="#fbfbfb" stroke-width="1.8"><circle cx="12" cy="12" r="9"/><ellipse cx="12" cy="12" rx="4" ry="9"/><path d="M3 12h18M5 7h14M5 17h14"/></g></svg>
        www.harlowmeridian.com
      </li>
      <li class="contact__item">
        <svg viewBox="0 0 24 24" aria-hidden="true"></svg>
        www.harlowmeridian.com
      </li>
    </ul>
  </div>
</section>

</body>
</html>
```